KRT Engineering Business Card Design

We’re looking for an elegant, clean, and timeless business card design that communicates experience, capability, and reliability.

KRT Engineering was established in 1995 , we are a Government Contracting company providing Professional Services to the Office of Frontier Affairs, Harbor Protection and the Vantage Collective. Our capabilities include: Acquisition & Program Management; Intelligence & Security Operations; Cyber, IT & Network Operations; Lifecycle Logistics & Asset Readiness; C5ISR Systems Engineering & Sustainment.

We want the card to reflect a straightforward, confident approach to business. The design should feel polished and professional without being flashy or overly corporate.

Design Direction
Clean, sophisticated, and uncluttered
Elegant but understated
Strong typography and thoughtful spacing
A timeless aesthetic rather than something overly trendy
Confident and established, with a sense of substance
Easy to read and practical in a real-world business setting

The overall impression should be: “These are experienced professionals who know what they’re doing, do what they say, and can be relied upon.”

We’re open to creative interpretations. The finished card should feel distinctive through its typography, proportions, layout, and attention to detail rather than through excessive graphics or visual effects.

We’re looking for a design that would make a potential client immediately feel that they’re dealing with a capable, trustworthy, and established company.

Company Colors: Navy and Gold/Yellow (but you do not need to use these colors on the card)
Company Name: KRT Engineering Associates, Inc. (known as KRT Engineering)
Website: krtengineering.com
Company Logo: Navy & Gold (other variations attached)

```html
<!DOCTYPE html>
<html lang="en">
<head>
<meta charset="utf-8">
<title>KRT Engineering — Business Card</title>
<link rel="stylesheet" href="https://fonts.googleapis.com/css2?family=Montserrat:wght@600;700;800&family=Lato:wght@400;700&display=swap">
<style>
  :root {
    --navy: #1f2a63;
    --navy-deep: #18214f;
    --gold: #fbe04d;
    --gold-muted: #b8aa52;
    --white: #ffffff;
    --stage: #2e2e2e;
    --ink: #1f2a63;
  }
  * { box-sizing: border-box; margin: 0; padding: 0; }
  html, body { width: 1200px; height: 1000px; overflow: hidden; }
  body {
    background: var(--stage);
    font-family: "Lato", sans-serif;
    position: relative;
  }
  .card {
    position: absolute;
    top: 346px;
    width: 540px;
    height: 309px;
    border-radius: 16px;
    overflow: hidden;
    box-shadow: 0 18px 40px rgba(0,0,0,0.45);
  }
  .card--back { left: 40px; }
  .card--front { left: 620px; }
  .card__art { position: absolute; inset: 0; width: 100%; height: 100%; }

  .wordmark {
    position: absolute;
    font-family: "Montserrat", sans-serif;
    font-weight: 800;
    letter-spacing: 0.02em;
    line-height: 1;
  }
  .card--back .wordmark {
    left: 0; right: 0; top: 112px;
    text-align: center;
    font-size: 96px;
    color: var(--white);
  }
  .card--front .wordmark {
    left: 268px; top: 244px;
    font-size: 40px;
    color: var(--navy);
  }

  .holder {
    position: absolute;
    left: 30px; top: 86px;
    color: var(--white);
  }
  .holder__name {
    font-family: "Montserrat", sans-serif;
    font-weight: 700;
    font-size: 22px;
    letter-spacing: 0.04em;
    color: var(--gold);
    text-transform: uppercase;
  }
  .holder__title {
    margin-top: 5px;
    font-size: 13px;
    letter-spacing: 0.02em;
  }

  .contact {
    position: absolute;
    left: 374px; top: 156px;
    color: var(--ink);
    font-size: 11px;
    line-height: 1.45;
  }
  .contact__company { font-weight: 700; }
  .contact__list { list-style: none; margin-top: 6px; }
  .contact__list li { display: flex; align-items: center; gap: 7px; }
  .contact__list svg { width: 10px; height: 10px; flex: none; }
</style>
</head>
<body>

  <section class="card card--back" aria-label="Card back">
    <svg class="card__art" viewBox="0 0 540 309" preserveAspectRatio="none">
      <defs>
        <linearGradient id="backPhotoTone" x1="0" y1="0" x2="1" y2="1">
          <stop offset="0" stop-color="#b8aa52"/>
          <stop offset="0.35" stop-color="#6e6a5e"/>
          <stop offset="0.62" stop-color="#1f2a63"/>
          <stop offset="1" stop-color="#1f2a63"/>
        </linearGradient>
      </defs>
      <rect width="540" height="309" fill="var(--navy)"/>
      <rect width="540" height="309" fill="url(#backPhotoTone)" role="img" aria-label="Photo of a military jet aircraft, tinted navy and gold"/>
    </svg>
    <div class="wordmark">KRT</div>
  </section>

  <section class="card card--front" aria-label="Card front">
    <svg class="card__art" viewBox="0 0 540 309" preserveAspectRatio="none">
      <defs>
        <linearGradient id="frontPhotoTone" x1="0" y1="0" x2="1" y2="0">
          <stop offset="0" stop-color="#1f2a63"/>
          <stop offset="0.55" stop-color="#4a5790"/>
          <stop offset="1" stop-color="#8a8fb8"/>
        </linearGradient>
      </defs>
      <rect class="panel-navy" width="540" height="309" fill="var(--navy)"/>
      <path d="M300,0 L540,0 L540,52 C450,66 380,96 330,132 Z" fill="url(#frontPhotoTone)" opacity="0.85" role="img" aria-label="Photo of an aircraft cockpit and equipment lights"/>
      <path class="band-gold" d="M182,309 C250,168 392,72 540,50 L540,92 C404,108 282,188 216,309 Z" fill="var(--gold)"/>
      <path class="panel-white" d="M216,309 C282,188 404,108 540,92 L540,309 Z" fill="var(--white)"/>
    </svg>

    <div class="holder">
      <div class="holder__name">Marla Venturi</div>
      <div class="holder__title">President, CEO &amp; Founder</div>
    </div>

    <div class="wordmark">KRT</div>

    <div class="contact">
      <div class="contact__company">KRT Engineering Associates, Inc</div>
      <div>4820 Harrow Lane, Suite 310</div>
      <div>Bayport, VA 23999</div>
      <ul class="contact__list">
        <li>
          <svg viewBox="0 0 10 10"><path d="M2 1 L4 1 L4.6 3 L3.5 4 C4 5.3 4.8 6.1 6 6.6 L7 5.5 L9 6 L9 8 C5 8.5 1.5 5 2 1 Z" fill="var(--navy)"/></svg>
          555-010-4827
        </li>
        <li>
          <svg viewBox="0 0 10 10"><rect x="2.5" y="0.5" width="5" height="9" rx="1" fill="none" stroke="var(--navy)" stroke-width="1.2"/><circle cx="5" cy="8" r="0.6" fill="var(--navy)"/></svg>
          555-010-4827
        </li>
        <li>
          <svg viewBox="0 0 10 10"><rect x="0.5" y="2" width="9" height="6" fill="var(--navy)"/><path d="M0.5 2 L5 5.5 L9.5 2" fill="none" stroke="var(--white)" stroke-width="0.9"/></svg>
          info@krtengineering.com
        </li>
        <li>
          <svg viewBox="0 0 10 10"><circle cx="5" cy="5" r="4.3" fill="none" stroke="var(--navy)" stroke-width="1.1"/><path d="M0.7 5 H9.3 M5 0.7 C3 3 3 7 5 9.3 M5 0.7 C7 3 7 7 5 9.3" fill="none" stroke="var(--navy)" stroke-width="0.8"/></svg>
          krtengineering.com
        </li>
      </ul>
    </div>
  </section>

</body>
</html>
```